7:40 Command Blueprint- A Handbook To Shape The Captain Others Could Trust

7:40 Command Blueprint
A Handbook To Shape The Captain Others Could Trust

It will be a 6 X 9 guide that is meant for people to keep with them with pages to fill out. See supporting pics for overall pillars that are discussed and form basis of the solution.

I will need a spine and back cover as well.

My blog and content: www.corvinmhale-example.com

Target Market(s)

Business professionals, senior emergency services people

Industry/Entity Type

Business Management

Font styles to use
Serif

Colors

Designer to choose colors to be used in the design.

Requirements
Must have
• Clean look, easily recognizable among other books. Front cover and back and spine. My picture on the back somewhere (corner maybe?!)
Nice to have
• Easily recognizeable
• NOTE: Graphic should read Today, Was I the Leader That I Would Want? I uploaded graphic that says ..."I Would've Wanted" which is incorrect.
Should not have
• Busy cover

```html
<!DOCTYPE html>
<html lang="en">
<head>
<meta charset="UTF-8">
<title>7:40 Command Blueprint – Book Cover Spread</title>
<link rel="stylesheet" href="https://fonts.googleapis.com/css2?family=Bebas+Neue&family=Oswald:wght@400&family=Arimo:wght@400&display=swap">
<style>
  :root {
    --canvas: #000000;
    --paper: #ffffff;
    --paper-shade: #e9ebee;
    --brand-blue: #1b4f9b;
    --ink: #111111;
    --rule: #555555;
    --portrait: #000000;
    --emblem-light: #eceef1;
    --emblem-mid: #c9cdd3;
    --pattern-light: #f4f5f7;
    --pattern-mid: #d9dde2;
  }
  * { margin: 0; padding: 0; box-sizing: border-box; }
  html, body {
    width: 1200px; height: 1200px; overflow: hidden;
    background: var(--canvas);
  }
  .spread {
    position: absolute; left: 33px; top: 218px;
    width: 1143px; height: 769px;
    background: linear-gradient(180deg, var(--paper) 0%, var(--paper) 55%, var(--paper-shade) 100%);
    overflow: hidden;
  }
  .floor-pattern {
    position: absolute; left: 0; right: 0; bottom: 0; height: 180px;
    background: linear-gradient(180deg, rgba(255,255,255,0) 0%, var(--pattern-light) 35%, var(--pattern-mid) 100%);
  }
  /* Back cover */
  .back-cover { position: absolute; left: 0; top: 0; width: 522px; height: 100%; }
  .back-title {
    position: absolute; left: 34px; top: 20px;
    font-family: "Bebas Neue", sans-serif; font-size: 50px; line-height: 1;
    font-weight: 400; color: var(--brand-blue); letter-spacing: 1.6px; white-space: nowrap;
  }
  .back-copy {
    position: absolute; left: 34px; width: 463px;
    font-family: "Arimo", sans-serif; font-size: 13.5px; line-height: 18.6px;
    color: var(--ink); text-align: justify;
  }
  .back-copy.intro { top: 82px; }
  .back-copy.pillars { top: 217px; }
  .back-rule {
    position: absolute; left: 34px; top: 462px; width: 463px; height: 1px;
    background: var(--rule);
  }
  .author-portrait {
    position: absolute; left: 37px; top: 490px; width: 107px; height: 142px;
    background: var(--portrait);
  }
  .author-bio {
    position: absolute; left: 159px; top: 487px; width: 338px;
    font-family: "Arimo", sans-serif; font-size: 13.5px; line-height: 18.6px;
    color: var(--ink); text-align: justify;
  }
  .back-website {
    position: absolute; left: 34px; top: 730px;
    font-family: "Arimo", sans-serif; font-size: 13px; color: var(--ink);
  }
  /* Spine */
  .spine { position: absolute; left: 522px; top: 0; width: 105px; height: 100%; }
  .spine-title, .spine-author {
    position: absolute; left: 50%; writing-mode: vertical-rl;
    transform: translateX(-50%); white-space: nowrap;
  }
  .spine-title {
    top: 28px; font-family: "Bebas Neue", sans-serif; font-size: 52px;
    line-height: 1; color: var(--brand-blue); letter-spacing: 2px;
  }
  .spine-author {
    top: 592px; font-family: "Oswald", sans-serif; font-size: 21px;
    color: var(--ink); letter-spacing: 0.5px;
  }
  /* Front cover */
  .front-cover { position: absolute; left: 627px; top: 0; width: 516px; height: 100%; }
  .front-title {
    position: absolute; left: 0; top: 0; width: 100%; height: 340px;
    font-family: "Bebas Neue", sans-serif; font-weight: 400; color: var(--brand-blue);
    letter-spacing: 1px;
  }
  .front-title span {
    position: absolute; left: 0; right: 0; text-align: center;
    line-height: 1; white-space: nowrap;
  }
  .front-title .title-number { top: 14px; font-size: 150px; }
  .front-title .title-line-one { top: 129px; font-size: 131px; }
  .front-title .title-line-two { top: 226px; font-size: 131px; }
  .subtitle-band {
    position: absolute; left: 33px; width: 452px; top: 352px; height: 27px;
    border-top: 1.5px solid var(--rule); border-bottom: 1.5px solid var(--rule);
    display: flex; align-items: center; justify-content: center;
    font-family: "Arimo", sans-serif; font-size: 13.5px; color: var(--ink);
    text-transform: uppercase; letter-spacing: 0.4px; white-space: nowrap;
  }
  .emblem-area {
    position: absolute; left: 300px; top: 487px; width: 120px; height: 120px;
    background: radial-gradient(circle, var(--emblem-mid) 0%, var(--emblem-light) 45%, rgba(236,238,241,0) 70%);
  }
  .front-author {
    position: absolute; left: 0; right: 0; top: 660px; text-align: center;
    font-family: "Oswald", sans-serif; font-size: 31px; color: var(--ink);
    letter-spacing: 0.5px;
  }
</style>
</head>
<body>
  <main class="spread">
    <div class="floor-pattern" role="img" aria-label="Soft field of small raised diamond tiles across the lower cover"></div>

    <section class="back-cover">
      <h2 class="back-title">7:40 Command Blueprint</h2>
      <p class="back-copy intro">Every shift, every meeting and every call asks the same quiet question of the person in charge. This handbook turns that question into a daily habit, with short reflections, honest prompts and pages to fill in, so you can measure the gap between the leader you intend to be and the one your people actually meet.</p>
      <p class="back-copy pillars">Built around seven pillars drawn from decades in boardrooms and emergency command posts, the blueprint moves from trust and clarity to courage, care and accountability. Each chapter pairs a plain lesson with a field exercise you can finish in minutes, whether you lead a team of four or an operation of four hundred. Keep it in your bag, mark it up and return to it after hard days. Over time the notes you write become a record of growth, a mirror for your choices and a steady guide when pressure rises. Inside you will find weekly check-ins, team conversation guides and space to record lessons from every incident, project and review, so your growth stays visible long after the moment has passed. Ask yourself each evening: today, was I the leader that I would want? Then use these pages to make tomorrow's answer a little closer to yes.</p>
      <div class="back-rule"></div>
      <div class="author-portrait" role="img" aria-label="Author portrait photograph"></div>
      <p class="author-bio">Corvin M. Hale has spent a career leading crews, managers and volunteers through crises large and small. He writes and speaks on practical leadership for business and emergency services professionals, and shares fresh tools and stories each week on his blog. He lives near the coast with his family and still keeps a worn notebook in every jacket he owns.</p>
      <p class="back-website">www.corvinmhale-example.com</p>
    </section>

    <section class="spine">
      <span class="spine-title">7:40 Command Blueprint</span>
      <span class="spine-author">CORVIN M. HALE</span>
    </section>

    <section class="front-cover">
      <h1 class="front-title">
        <span class="title-number">7:40</span>
        <span class="title-line-one">COMMAND</span>
        <span class="title-line-two">BLUEPRINT</span>
      </h1>
      <p class="subtitle-band">A Handbook To Shape The Captain Others Could Trust</p>
      <div class="emblem-area" role="img" aria-label="Compass illustration with a red needle and a dotted path"></div>
      <p class="front-author">CORVIN M. HALE</p>
    </section>
  </main>
</body>
</html>
```